Valdo Capital

We need a corporate style website design for a new company based in Shenzhen's Qianhai Special Economic Development Zone, China. We provide a range of financial services to large international investment companies. Typically these companies invest over 5 million RMB. The company is part of a group that consists of NorthKilns, ValdoTrusts and ValdoEquity. Our location and gateway into Qianhai Special Economic Zone is our core advantage. We would like to see designs that Do Not use purple and orange. The website design should be similar to other websites in this family but different enough to give it a unique style (See attached website links for reference). The final design should communicate financial safety and growth. This website will act partly as a business chamber with connections to the government so we would like it to be diplomatic in style.

www.northkilns.example
www.valdotrusts.example

*Nevegation Bar
Should including Homepage, Financial Product, Team, News.
Could refer to www.valdotrusts.example

*Contact Details

Miss Lan
Address:E 728, North Block, KMO Centre, East Sector, Shenzhen Bright Science Campus
Telephone: +86 0755 63920417
Cellphone: +86 13957280316

* Social Media
Should be grouped like:
1. Weibo QRcode+ Weibo
2. Facebook, Twitter, Linkedin.

Industry/Entity Type

Investment

```html
<!DOCTYPE html>
<html lang="en">
<head>
<meta charset="utf-8">
<title>Valdo Capital</title>
<link rel="stylesheet" href="https://fonts.googleapis.com/css2?family=Open+Sans:wght@400;600;700&family=Raleway:wght@400;500;600&display=swap">
<style>
:root{
  --blue:#1fa7e4;
  --band:#7fa7d9;
  --ink:#333333;
  --muted:#8a8a8a;
  --line:#dcdcdc;
  --dark:#2f3033;
  --darker:#232427;
  --footer-text:#b9b9b9;
  --white:#ffffff;
}
*{margin:0;padding:0;box-sizing:border-box}
html,body{width:818px;height:1200px;overflow:hidden;background:var(--white)}
body{position:relative;font-family:"Open Sans",Arial,sans-serif;color:var(--ink)}
.abs{position:absolute}

/* header */
.site-header{left:0;top:0;width:818px;height:58px;background:var(--white);box-shadow:0 2px 3px rgba(0,0,0,.18);z-index:3}
.brand{left:76px;top:14px;display:flex;align-items:center;gap:8px}
.brand-mark{width:22px;height:22px;background:#1f4f6e}
.brand-name{font-size:17px;font-weight:600;color:#1f2a33;letter-spacing:.5px}
.lang{left:626px;top:9px;font-size:8.5px;color:#555}
.lang u{color:#333}
.social-top{top:8px;width:17px;height:17px;border-radius:50%;background:#e6e6e6}
.main-nav{left:486px;top:37px;display:flex;gap:0;font-size:10px;font-weight:600;color:#444}
.main-nav span{position:absolute;white-space:nowrap}
.main-nav .active{color:var(--blue)}

/* hero */
.hero{left:0;top:58px;width:818px;height:362px;background:linear-gradient(100deg,#3a4560 0%,#9aa9bf 35%,#dfe6ef 55%,#56698c 75%,#c9d3df 100%)}
.hero-caption{left:75px;top:286px;width:254px;height:78px;background:rgba(20,22,28,.75);border-left:3px solid var(--blue);padding:6px 0 0 13px;color:var(--white)}
.hero-caption h1{font-size:19px;font-weight:600;line-height:24px}
.hero-caption p{font-size:8.8px;line-height:13.5px;color:#e5e5e5}
.hero-caption .more{font-size:8.5px;margin-top:2px}

/* services */
.services{left:75px;top:364px;width:668px;height:242px;background:var(--white);box-shadow:0 1px 3px rgba(0,0,0,.15)}
.services-band{left:0;top:0;width:668px;height:30px}
.services-title{left:13px;top:8px;font-family:"Raleway",sans-serif;font-size:13px;font-weight:500;color:#222}
.arrow-btn{top:6px;width:18px;height:18px;border-radius:50%;background:#eef1f5;border:1px solid #c9d3e0}
.card{top:43px;width:157px}
.card .photo{width:157px;height:96px;border:3px solid #ececec}
.card h3{font-family:"Raleway",sans-serif;font-size:12px;font-weight:500;margin-top:13px;color:#222}
.card p{font-size:8.6px;line-height:12.2px;color:var(--muted);margin-top:4px}
.card a{font-size:8.6px;color:#555;text-decoration:underline;display:block;margin-top:2px}

/* section dividers */
.divider{height:0;border-top:3px dotted #e2e2e2}
.section-title{font-family:"Raleway",sans-serif;font-size:13px;font-weight:500;color:#222;text-align:center}

/* about */
.about-heading{left:81px;top:655px;font-size:13.5px;color:#555}
.about-heading b{color:var(--blue);font-weight:700;font-family:"Raleway",sans-serif}
.about-text{left:82px;top:682px;width:400px;font-size:9.4px;line-height:13.6px;color:var(--muted)}
.about-text p+p{margin-top:13.6px}
.video{left:500px;top:683px;width:235px;height:143px;background:#222;box-shadow:0 2px 4px rgba(0,0,0,.3)}
.video-frame{left:1px;top:1px;width:233px;height:120px;background:linear-gradient(120deg,#2a2a2a,#6b6f74 55%,#2b2b2b)}
.video-bar{left:0;top:124px;width:235px;height:19px;background:#1b1b1b}

/* customers */
.customer{top:905px;font-family:"Raleway",sans-serif;color:#555;text-align:center;white-space:nowrap}

/* footer */
.footer{left:0;top:978px;width:818px;height:184px;background:var(--dark);overflow:hidden}
.footer-bottom{left:0;top:1162px;width:818px;height:38px;background:var(--darker);font-size:8.8px;color:var(--footer-text)}
.f-head{font-size:10.5px;color:#e2e2e2;display:flex;align-items:center;gap:6px}
.f-head i{display:block;height:1px;background:#555}
.f-text{font-size:8.4px;line-height:13.8px;color:var(--footer-text)}
.f-text u{text-decoration:underline}
.f-social{top:1053px;width:22px;height:22px;background:#2f7fc0;border-radius:2px}
.newsletter{left:551px;top:1101px;width:182px;height:22px;background:var(--white);border:1px solid #ccc}
.newsletter span{position:absolute;left:9px;top:5px;font-size:7.6px;font-style:italic;color:#555}
.subscribe{position:absolute;right:1px;top:1px;width:57px;height:18px;background:var(--blue);color:var(--white);font-size:8.8px;text-align:center;line-height:18px}
</style>
</head>
<body>

<header class="abs site-header">
  <div class="abs brand"><div class="brand-mark"></div><div class="brand-name">VALDO CAPITAL</div></div>
  <div class="abs lang"><u>EN</u> | SP &#9662;</div>
  <div class="abs social-top" style="left:681px"></div>
  <div class="abs social-top" style="left:703px"></div>
  <div class="abs social-top" style="left:725px"></div>
  <nav class="abs main-nav">
    <span class="active" style="left:0">HOME</span>
    <span style="left:53px">FINANCIAL PRODUCTS</span>
    <span style="left:180px">TEAM</span>
    <span style="left:231px">NEWS</span>
  </nav>
</header>

<section class="abs hero" role="img" aria-label="Photo of four business people in suits meeting around a table"></section>
<div class="abs hero-caption">
  <h1>Valdo Capital</h1>
  <p>Lorem ipsum dolor sit amet, consectetur adipisicing elit,<br>sed do eiusmod tempor incididunt magna aliqua..</p>
  <div class="more">Read More &#9656;</div>
</div>

<section class="abs services">
  <svg class="abs services-band" width="668" height="30" viewBox="0 0 668 30">
    <polygon points="123,0 668,0 668,30 143,30" fill="var(--band)"/>
  </svg>
  <div class="abs services-title">OUR SERVICES</div>
  <div class="abs arrow-btn" style="left:615px"><svg width="16" height="16"><path d="M9 5 L6 8 L9 11" stroke="#666" fill="none" stroke-width="1.3"/></svg></div>
  <div class="abs arrow-btn" style="left:638px"><svg width="16" height="16"><path d="M7 5 L10 8 L7 11" stroke="#666" fill="none" stroke-width="1.3"/></svg></div>

  <div class="abs card" style="left:7px">
    <div class="photo" role="img" aria-label="Photo of business people shaking hands" style="background:linear-gradient(135deg,#5a6270,#c8ccd2 60%,#3a3f48)"></div>
    <h3>Consultancy</h3>
    <p>Lorem ipsum dolor sit amet, consectetur adipisicing elit, sed do eiusmod tempor incididunt ut magna aliqua..</p>
    <a>Read More</a>
  </div>
  <div class="abs card" style="left:172px">
    <div class="photo" role="img" aria-label="Photo of a hand signing a document" style="background:linear-gradient(135deg,#b59a86,#eeeeee 55%,#6e655e)"></div>
    <h3>Insurance</h3>
    <p>Lorem ipsum dolor sit amet, consectetur adipisicing elit, sed do eiusmod tempor incididunt ut magna aliqua..</p>
    <a>Read More</a>
  </div>
  <div class="abs card" style="left:337px">
    <div class="photo" role="img" aria-label="Photo of a boardroom meeting with a chart on screen" style="background:linear-gradient(180deg,#dfe4ea,#9aa4ae 60%,#4a3a32)"></div>
    <h3>Capital Markets</h3>
    <p>Lorem ipsum dolor sit amet, consectetur adipisicing elit, sed do eiusmod tempor incididunt ut magna aliqua..</p>
    <a>Read More</a>
  </div>
  <div class="abs card" style="left:502px">
    <div class="photo" role="img" aria-label="Photo of colleagues reviewing papers at a desk" style="background:linear-gradient(135deg,#e7cf9e,#f3efe6 50%,#8a8f95)"></div>
    <h3>Property Management</h3>
    <p>Lorem ipsum dolor sit amet, consectetur adipisicing elit, sed do eiusmod tempor incididunt ut magna aliqua..</p>
    <a>Read More</a>
  </div>
</section>

<div class="abs divider" style="left:75px;top:630px;width:290px"></div>
<div class="abs section-title" style="left:365px;top:624px;width:88px">ABOUT US</div>
<div class="abs divider" style="left:453px;top:630px;width:290px"></div>

<h2 class="abs about-heading"><b>VALDO CAPITAL</b> Provide a Range of Financial Services</h2>
<div class="abs about-text">
  <p>Lorem ipsum dolor sit amet, consectetur adipisicing elit, sed do eiusmod tempor incididunt ut labore et dolore magna aliqua. Ut enim ad minim veniam, quis nostrud exercitation ullamco laboris nisi ut aliquip ex ea commodo consequat. Duis aute irure dolor in reprehenderit in voluptate velit esse cillum dolore eu fugiat nulla pariatur. Excepteur sint occaecat cupidatat non proident, sunt in culpa qui officia deserunt mollit anim id est laborum.</p>
  <p>Duis aute irure dolor in reprehenderit in voluptate velit esse cillum dolore eu fugiat nulla pariatur. Excepteur sint occaecat cupidatat non proident, sunt in culpa qui officia deserunt mollit anim id est laborum. Ut enim ad minim veniam, quis nostrud exercitation ullamco laboris nisi ut aliquip ex ea commodo consequat.</p>
</div>
<div class="abs video">
  <div class="abs video-frame" role="img" aria-label="Video still of hands holding a financial report"></div>
  <svg class="abs" style="left:92px;top:41px" width="52" height="52" viewBox="0 0 52 52">
    <circle cx="26" cy="26" r="25" fill="rgba(0,0,0,.45)"/>
    <polygon points="20,15 37,26 20,37" fill="#d8d8d8"/>
  </svg>
  <div class="abs video-bar">
    <svg width="235" height="19" viewBox="0 0 235 19">
      <polygon points="7,6 12,9.5 7,13" fill="#fff"/>
      <rect x="16" y="8" width="128" height="3" fill="#444"/>
      <rect x="16" y="8" width="72" height="3" fill="#c8161d"/>
      <text x="166" y="12.5" font-size="6.5" fill="#ddd" font-family="Open Sans,sans-serif">1:26 / 3:22</text>
      <polygon points="168,9.5 172,7 172,12" fill="#fff" transform="translate(42 0)"/>
      <rect x="218" y="8" width="0" height="3" fill="#c8161d"/>
      <rect x="176" y="8" width="18" height="3" fill="#c8161d" transform="translate(42 0) scale(0.8 1)"/>
      <rect x="204" y="7" width="7" height="5" fill="none" stroke="#fff"/>
      <text x="218" y="12.5" font-size="7" font-weight="700" font-style="italic" fill="#fff" font-family="Open Sans,sans-serif">HD</text>
    </svg>
  </div>
</div>

<div class="abs divider" style="left:75px;top:867px;width:270px"></div>
<div class="abs section-title" style="left:345px;top:861px;width:128px">OUR CUSTOMERS</div>
<div class="abs divider" style="left:475px;top:867px;width:268px"></div>

<div class="abs customer" style="left:86px;width:80px;font-size:14px">Harbor Lodge</div>
<div class="abs customer" style="left:205px;width:118px;font-size:20px">Brent&amp;Hale</div>
<div class="abs customer" style="left:368px;width:90px;font-size:20px">Corvane</div>
<div class="abs customer" style="left:500px;width:92px;font-size:18px;font-weight:600">Lumetra</div>
<div class="abs customer" style="left:628px;width:108px;font-size:17px">Sandel City</div>

<footer class="abs footer">
  <svg class="abs" style="left:0;top:0" width="818" height="184" viewBox="0 0 818 184">
    <polygon points="330,184 818,20 818,184" fill="#3a3b3f"/>
  </svg>
</footer>
<div class="abs f-head" style="left:82px;top:1010px">Contact Info <i style="width:44px"></i></div>
<div class="abs f-text" style="left:82px;top:1038px;width:130px">
  <u>Address: E 728, North Block,<br>KMO Centre, East Sector,<br>Shenzhen Bright Science<br>Campus</u><br>
  <u>eMail: info@valdocapital.example</u><br>
  <u>Phone: +86 0755 63920417</u>
</div>
<div class="abs f-head" style="left:227px;top:1010px">About Us <i style="width:96px"></i></div>
<div class="abs f-text" style="left:227px;top:1038px;width:150px">Lorem ipsum dolor sit amet, consectetur adipisicing elit, sed do eiusmod tempor incididunt ut labore et dolore magna aliqua. Ut enim ad minim veniam.</div>
<div class="abs f-head" style="left:409px;top:1010px">Company Info <i style="width:36px"></i></div>
<div class="abs f-text" style="left:409px;top:1038px">
  <u>Lorem ipsum</u><br><u>dolor sit amet</u><br><u>consectetur</u><br><u>adipsicing elit</u>
</div>
<div class="abs f-head" style="left:551px;top:1010px">Stay updates on our Socail Network <i style="width:10px"></i></div>
<div class="abs f-social" style="left:552px"></div>
<div class="abs f-social" style="left:583px;background:#3aa3e0"></div>
<div class="abs f-social" style="left:614px;background:#1b76b3"></div>
<div class="abs f-head" style="left:551px;top:1078px">Join Our Newsletter <i style="width:88px"></i></div>
<div class="abs newsletter"><span>Enter your email address</span><div class="subscribe">Subscribe</div></div>

<div class="abs footer-bottom">
  <span class="abs" style="left:83px;top:13px">Home</span>
  <span class="abs" style="left:120px;top:13px">Financial Products</span>
  <span class="abs" style="left:206px;top:13px">Team</span>
  <span class="abs" style="left:241px;top:13px">News</span>
  <span class="abs" style="left:580px;top:13px">&copy; Copyrights 2014 All rights Reserved</span>
</div>

</body>
</html>
```